Document Processing Services and Solutions for School Systems

I am looking to design a brochure for both Digital and Paper use. I can supply the written content. Would be looking for an overall design of the brochure with provided content worked into it.

```html
<!DOCTYPE html>
<html lang="en">
<head>
<meta charset="utf-8">
<title>Meridian Records – Bifold Brochure</title>
<link href="https://fonts.googleapis.com/css2?family=Montserrat:wght@400;500;600;700&family=Oswald:wght@600;700&family=Poppins:ital,wght@0,600;0,700;0,800;1,700;1,800;1,900&display=swap" rel="stylesheet">
<style>
:root{
  --navy:#2e2d8f;
  --navy-deep:#23226e;
  --gold:#c99a0a;
  --gold-light:#dcae22;
  --ink:#1f1f3a;
  --paper:#ffffff;
  --stage:#eef0f4;
  --rule:#d9d9e6;
}
*{box-sizing:border-box;margin:0;padding:0}
html,body{width:723px;height:1200px;overflow:hidden}
body{background:var(--stage);font-family:"Montserrat",sans-serif;color:var(--ink);position:relative}
.spread{position:absolute;left:72px;width:579px;height:447px;background:var(--paper);box-shadow:0 4px 14px rgba(20,20,60,.18);overflow:hidden}
.spread--outside{top:96px}
.spread--inside{top:671px}
.abs{position:absolute;z-index:3}
.layer-bg{position:absolute;z-index:0}
.photo{position:absolute;z-index:1}
.fold{position:absolute;left:290px;top:0;width:1px;height:100%;background:rgba(0,0,0,.06);z-index:2}

/* brand name */
.brand{position:absolute;z-index:3;font-family:"Poppins",sans-serif;font-weight:700;color:var(--navy);line-height:1;letter-spacing:-.3px;display:flex;align-items:center;gap:4px}
.brand__dot{width:5px;height:5px;background:var(--gold)}

/* outside – back */
.back-bg{left:120px;top:0;width:170px;height:269px;background:linear-gradient(90deg,#fff 0%,#dcdcdf 45%,#c9c9cc 100%);z-index:0}
.back-photo{left:0;top:175px;width:215px;height:94px;background:linear-gradient(135deg,#e9e6e2 0%,#b9a89a 45%,#6d4f48 75%,#d07264 100%)}
.cta-headline{left:28px;top:124px;font-family:"Poppins",sans-serif;font-style:italic;font-weight:900;font-size:14px;line-height:13px;color:var(--navy)}
.cta-headline em{color:var(--gold);font-style:italic}
.back-panel{left:0;top:269px;width:290px;height:102px;background:var(--navy)}
.back-panel__intro{left:28px;top:284px;font-size:8.2px;font-weight:600;color:#fff;line-height:10px;white-space:nowrap}
.back-panel__rule{left:28px;top:306px;width:190px;height:1px;background:rgba(255,255,255,.3)}
.back-panel__offer{left:28px;top:309px;font-family:"Poppins",sans-serif;font-weight:800;font-size:14px;line-height:15px;color:var(--gold-light);white-space:nowrap}
.back-panel__offer span{color:#fff}
.back-panel__note{left:28px;top:344px;font-size:6.1px;font-weight:600;color:#fff;line-height:8px;white-space:nowrap}
.back-rule{left:0;top:371px;width:290px;height:3px;background:var(--gold)}
.contact{left:137px;top:394px;list-style:none}
.contact li{display:flex;align-items:center;gap:5px;font-size:6.6px;font-weight:600;color:var(--navy);line-height:10px}
.contact li::before{content:"";width:5px;height:5px;border-radius:50%;background:var(--gold)}
.bottom-rule{left:0;top:444px;width:579px;height:3px;background:var(--navy);z-index:2}

/* outside – front */
.front-woman{left:248px;top:160px;width:152px;height:284px;border-radius:70px 70px 6px 6px;background:linear-gradient(180deg,#e8c3a6 0%,#d69e82 30%,#f3f1ee 48%,#c9b36a 62%,#e5e5e7 80%,#bfbfc4 100%)}
.tag{position:absolute;z-index:3;font-family:"Poppins",sans-serif;font-style:italic;font-weight:800;background:var(--gold);clip-path:polygon(0 0,100% 0,96% 100%,0 100%)}
.tag--transform{left:401px;top:89px;width:148px;height:17px;font-size:11.5px;line-height:17px;color:var(--navy);padding-left:7px}
.front-title{left:401px;top:113px;font-family:"Oswald",sans-serif;font-weight:700;font-size:31px;line-height:27px;color:var(--navy);transform:scaleX(.86);transform-origin:left;letter-spacing:-.5px}
.front-band{left:356px;top:219px;width:223px;height:52px;background:var(--navy);clip-path:polygon(6% 0,100% 0,100% 100%,0 100%)}
.tag--with{left:401px;top:210px;width:72px;height:15px;font-size:9.5px;line-height:15px;color:#fff;padding-left:4px}
.front-band__text{left:407px;top:232px;font-family:"Poppins",sans-serif;font-style:italic;font-weight:800;font-size:14px;line-height:13.5px;color:#fff;white-space:nowrap}
.pillars{left:472px;top:288px;width:83px;list-style:none}
.pillars li{font-family:"Poppins",sans-serif;font-style:italic;font-weight:800;font-size:11px;line-height:14px;color:var(--navy);border-bottom:1px solid var(--rule)}
.pillars li:last-child{border-bottom:0}
.front-copy{left:427px;top:344px;width:135px;font-size:5.5px;font-weight:500;line-height:7px;color:var(--ink)}
.url-bar{left:401px;top:405px;width:151px;height:16px;background:var(--navy);clip-path:polygon(3% 0,100% 0,97% 100%,0 100%)}
.url-bar::before{content:"";position:absolute;left:0;top:0;width:22px;height:100%;background:var(--gold)}
.url-bar span{position:absolute;left:26px;top:0;font-size:8.6px;font-weight:500;line-height:16px;color:#fff}

/* inside */
.inside-fade{left:290px;top:0;width:289px;height:447px;background:linear-gradient(90deg,#d8d8dc 0%,#f3f3f5 14%,#fff 40%)}
.section-title{font-family:"Poppins",sans-serif;font-style:italic;font-weight:900;font-size:20.5px;line-height:18px;color:var(--navy)}
.section-title em{color:var(--gold);font-style:italic;display:block}
.service{position:absolute;z-index:3;left:0;width:290px;border-top:1.5px solid var(--gold);border-bottom:1.5px solid var(--gold)}
.service__icon{position:absolute;left:28px;top:8px;width:26px;height:26px;border-radius:50%;background:var(--navy);border:2px solid var(--gold);display:flex;align-items:center;justify-content:center}
.service__title{position:absolute;left:62px;top:8px;font-family:"Poppins",sans-serif;font-style:italic;font-weight:800;font-size:10px;line-height:9.3px;color:var(--navy)}
.service__list{position:absolute;left:28px;list-style:none;width:135px}
.service__list li{position:relative;padding-left:7px;font-size:5.6px;font-weight:500;line-height:7px;margin-bottom:6px;color:var(--ink)}
.service__list li::before{content:"";position:absolute;left:0;top:2px;width:3.5px;height:3.5px;border-radius:50%;border:.8px solid var(--gold)}
.service__photo{position:absolute;left:165px;width:103px;height:103px;border-radius:50%;border:1.5px solid var(--gold)}
.benefits{left:328px;top:98px;width:251px;height:276px;background:var(--navy);border-radius:12px 0 0 12px}
.benefit{position:absolute;z-index:3;left:313px;width:170px}
.benefit__icon{position:absolute;left:0;top:0;width:35px;height:35px;border-radius:50%;background:var(--gold);border:2px solid #fff;box-shadow:0 0 0 1.5px var(--gold);display:flex;align-items:center;justify-content:center}
.benefit__title{position:absolute;left:46px;top:0;font-family:"Poppins",sans-serif;font-style:italic;font-weight:700;font-size:10.2px;line-height:12px;color:var(--gold-light);white-space:nowrap}
.benefit__text{position:absolute;left:46px;top:14px;font-size:7px;line-height:8.7px;color:#fff;white-space:nowrap}
.benefit-rule{position:absolute;z-index:2;left:359px;width:116px;height:1px;background:rgba(255,255,255,.25)}
.inside-woman{left:437px;top:160px;width:142px;height:287px;border-radius:50px 0 0 0;clip-path:polygon(30% 0,100% 0,100% 100%,0 100%,0 58%,28% 46%);background:linear-gradient(180deg,#ecd08c 0%,#e2b88f 28%,#f1efec 52%,#3fb8c9 72%,#e36b52 86%,#2a2a2a 100%)}
.inside-url{left:328px;top:400px;font-size:9px;font-weight:500;color:var(--ink)}
</style>
</head>
<body>

<section class="spread spread--outside">
  <div class="layer-bg back-bg" role="img" aria-label="Faded background photo of stacked office binders and file servers"></div>
  <div class="photo back-photo" role="img" aria-label="Photo of two colleagues reviewing documents at a desk with a computer"></div>
  <h2 class="abs cta-headline">GET<br>STARTED<br><em>TODAY!</em></h2>

  <div class="layer-bg back-panel"></div>
  <p class="abs back-panel__intro">LET US HELP YOU MODERNIZE YOUR<br>DOCUMENT PROCESSING SYSTEM.</p>
  <div class="abs back-panel__rule"></div>
  <p class="abs back-panel__offer">CONTACT US FOR A<br><span>FREE</span> CONSULTATION</p>
  <p class="abs back-panel__note">and discover how our solutions can transform your<br>school's document management.</p>
  <div class="layer-bg back-rule"></div>

  <div class="brand" style="left:28px;top:398px;font-size:17px"><span class="brand__dot"></span>Meridian</div>
  <ul class="abs contact">
    <li>555-014-2290</li>
    <li>info@meridianrecords.com</li>
    <li>www.meridianrecords.com</li>
  </ul>

  <div class="fold"></div>

  <div class="brand" style="left:432px;top:38px;font-size:21px"><span class="brand__dot"></span>Meridian</div>
  <div class="tag tag--transform">TRANSFORM YOUR</div>
  <h1 class="abs front-title">SCHOOL'S<br>DOCUMENT<br>MANAGEMENT</h1>
  <div class="layer-bg front-band"></div>
  <div class="tag tag--with">WITH OUR</div>
  <p class="abs front-band__text">COMPREHENSIVE<br>SOLUTIONS</p>

  <div class="photo front-woman" role="img" aria-label="Photo of a smiling woman carrying a tall stack of paper files and binders"></div>

  <ul class="abs pillars">
    <li>STREAMLINE</li>
    <li>SECURE</li>
    <li>SIMPLIFY</li>
  </ul>
  <p class="abs front-copy">Managing school documents efficiently is crucial for smooth operations, compliance, and productivity. Our document processing services provide innovative solutions tailored for educational institutions, ensuring secure and seamless document and data handling.</p>
  <div class="abs url-bar"><span>www.meridianrecords.com</span></div>

  <div class="bottom-rule"></div>
</section>

<section class="spread spread--inside">
  <div class="layer-bg inside-fade"></div>

  <h2 class="abs section-title" style="left:31px;top:24px">OUR<em>SERVICES</em></h2>
  <div class="brand" style="left:200px;top:32px;font-size:13px"><span class="brand__dot" style="width:4px;height:4px"></span>Meridian</div>

  <article class="service" style="top:74px;height:102px">
    <div class="service__icon"><svg width="12" height="12" viewBox="0 0 12 12" fill="none" stroke="#fff" stroke-width="1"><rect x="2.5" y="1.5" width="7" height="9" rx="1"/><line x1="1" y1="6" x2="11" y2="6"/></svg></div>
    <h3 class="service__title">DOCUMENT<br>SCANNING<br>&amp; CONVERSION</h3>
    <ul class="service__list" style="top:40px">
      <li>Convert paper records into digital formats for easy access and storage.</li>
      <li>High-speed scanning for student records, administrative files, and historical archives.</li>
      <li>OCR (Optical Character Recognition) for searchable and editable documents.</li>
    </ul>
    <div class="service__photo" style="top:-2px;background:linear-gradient(135deg,#e7e4df,#8d9aa8 55%,#2c3440)" role="img" aria-label="Photo of a woman scanning documents on an office scanner"></div>
  </article>

  <article class="service" style="top:194px;height:101px">
    <div class="service__icon"><svg width="12" height="12" viewBox="0 0 12 12" fill="none" stroke="#fff" stroke-width="1"><path d="M3 8h6.5a2 2 0 0 0 0-4 3 3 0 0 0-5.7-.5A2.3 2.3 0 0 0 3 8z"/><line x1="6" y1="8" x2="6" y2="11"/></svg></div>
    <h3 class="service__title">CLOUD-BASED<br>DOCUMENT<br>MANAGEMENT</h3>
    <ul class="service__list" style="top:40px">
      <li>Secure, centralized document storage accessible from anywhere.</li>
      <li>Role-based access controls for administrators, teachers, and staff.</li>
      <li>Automated backups and compliance with educational data security standards.</li>
    </ul>
    <div class="service__photo" style="top:-2px;background:radial-gradient(circle at 60% 50%,#5a7fb0 0%,#1c2a45 45%,#0c1222 100%)" role="img" aria-label="Photo of a hand touching a glowing cloud storage icon with folders"></div>
  </article>

  <article class="service" style="top:313px;height:102px">
    <div class="service__icon"><svg width="12" height="12" viewBox="0 0 12 12" fill="none" stroke="#fff" stroke-width="1"><circle cx="6" cy="6" r="4.5"/><path d="M5 4l3 2-3 2z" fill="#fff"/></svg></div>
    <h3 class="service__title">WORKFLOW<br>AUTOMATION</h3>
    <ul class="service__list" style="top:40px">
      <li>Digitize and streamline approval processes for enrollment, transcripts, and HR forms.</li>
      <li>Reduce paperwork and improve efficiency with automated workflows.</li>
      <li>Integration capable with existing school management systems.</li>
    </ul>
    <div class="service__photo" style="top:-2px;background:linear-gradient(160deg,#d9d4cf,#9b6a55 45%,#e9e9ea 70%,#3b3b3f)" role="img" aria-label="Photo of a bright open-plan office with computer desks"></div>
  </article>

  <div class="fold"></div>

  <h2 class="abs section-title" style="left:327px;top:24px">WHY<em>CHOOSE<br>US?</em></h2>
  <div class="brand" style="left:493px;top:32px;font-size:13px"><span class="brand__dot" style="width:4px;height:4px"></span>Meridian</div>

  <div class="layer-bg benefits"></div>

  <div class="photo inside-woman" role="img" aria-label="Photo of a woman with glasses holding a stack of colourful ring binders"></div>

  <div class="benefit" style="top:112px">
    <div class="benefit__icon"><svg width="16" height="16" viewBox="0 0 16 16" fill="none" stroke="#fff" stroke-width="1.2"><line x1="3" y1="14" x2="3" y2="10"/><line x1="7" y1="14" x2="7" y2="7"/><line x1="11" y1="14" x2="11" y2="4"/><path d="M2 8l5-4 3 2 4-4"/></svg></div>
    <h3 class="benefit__title">Increased Efficiency</h3>
    <p class="benefit__text">Save time with digital workflows<br>and instant document retrieval.</p>
  </div>
  <div class="benefit-rule" style="top:168px"></div>

  <div class="benefit" style="top:174px">
    <div class="benefit__icon"><svg width="16" height="16" viewBox="0 0 16 16" fill="none" stroke="#fff" stroke-width="1.2"><path d="M8 1.5l5 2v4c0 3.5-2.3 5.8-5 7-2.7-1.2-5-3.5-5-7v-4z"/><path d="M5.5 8l2 2 3-3.5"/></svg></div>
    <h3 class="benefit__title">Enhanced Security</h3>
    <p class="benefit__text">Protect sensitive student<br>&amp;faculty information.</p>
  </div>
  <div class="benefit-rule" style="top:232px"></div>

  <div class="benefit" style="top:236px">
    <div class="benefit__icon"><svg width="16" height="16" viewBox="0 0 16 16" fill="none" stroke="#fff" stroke-width="1.2"><circle cx="8" cy="6" r="3.5"/><path d="M1.5 12.5h4l2 1.5h5l2-2.5"/></svg></div>
    <h3 class="benefit__title">Cost Savings</h3>
    <p class="benefit__text">Reduce paper, printing,<br>and storage costs.</p>
  </div>
  <div class="benefit-rule" style="top:291px"></div>

  <div class="benefit" style="top:295px">
    <div class="benefit__icon"><svg width="16" height="16" viewBox="0 0 16 16" fill="none" stroke="#fff" stroke-width="1.2"><path d="M8 10V4"/><path d="M8 6c-2 0-3-1.5-3-3 2 0 3 1 3 3zM8 5c0-2 1.5-3 3-3 0 2-1.5 3-3 3z"/><path d="M1.5 12.5h4l2 1.5h5l2-2.5"/></svg></div>
    <h3 class="benefit__title">Eco-Friendly</h3>
    <p class="benefit__text">Minimize your school's<br>carbon footprint by<br>going digital.</p>
  </div>

  <p class="abs inside-url">www.meridianrecords.com</p>
</section>

</body>
</html>
```